Breakfast Cafe - The Sunny Nook

It is for my breakfast and lunch cafe with a hawaiian / beach theme. I am open 7 days a week from 7am to 2pm. We serve traditional American food such as omelettes, pancakes, burgers and sandwiches. I'll upload my old card and my new logo to be used. We have a lot of day to day regulars who eat there during the week, our t-shirts actually say 'Locals Only' on them. Hope this helps. Thanks.

Target Market(s)

anyone who has an appetite!

Industry/Entity Type

American Restaurant

Contact Information for Business Card

4815C Marlow Grove Avenue
Long Beach, California
(555) 731-2294

Requirements
Must have
• Address and phone number easily readable.
Nice to have
• beach or tropical theme

```html
<!DOCTYPE html>
<html lang="en">
<head>
<meta charset="utf-8">
<title>The Sunny Nook – Business Card</title>
<link href="https://fonts.googleapis.com/css2?family=Roboto+Condensed:wght@400;700&family=Lobster&display=swap" rel="stylesheet">
<style>
  :root {
    --backdrop: #222222;
    --card: #ffffff;
    --brown: #b5631a;
    --sky: #5bbdd6;
    --crimson: #c8103a;
    --ink: #555555;
    --rule: #d6d6d6;
    --sunset: #f39a3a;
  }
  * { margin: 0; padding: 0; box-sizing: border-box; }
  html, body {
    width: 1200px; height: 960px; overflow: hidden;
    background: var(--backdrop);
  }
  .business-card {
    position: absolute; left: 300px; top: 309px;
    width: 600px; height: 343px;
    background: var(--card);
    border-radius: 22px;
    overflow: hidden;
    font-family: "Roboto Condensed", "Arial Narrow", sans-serif;
  }
  .brand {
    position: absolute; left: 50px; top: 58px; width: 218px;
    display: flex; flex-direction: column; align-items: center;
  }
  .brand-mark {
    width: 172px; height: 172px; border-radius: 50%;
    background: radial-gradient(circle at 50% 40%, var(--sunset) 0%, #e0873a 55%, #8a4a1a 100%);
  }
  .brand-name {
    margin-top: 8px;
    font-size: 28px; font-weight: 700; color: var(--sky);
    line-height: 1; white-space: nowrap;
  }
  .divider {
    position: absolute; left: 290px; top: 62px;
    width: 1px; height: 205px; background: var(--rule);
  }
  .details { position: absolute; left: 318px; top: 68px; color: var(--ink); }
  .address { font-size: 17px; line-height: 21px; }
  .phone {
    display: flex; align-items: center; gap: 4px;
    margin-top: 13px; font-size: 23px; font-weight: 700;
  }
  .phone svg { width: 28px; height: 28px; }
  .tagline {
    margin-top: 11px; font-size: 16px; font-weight: 700;
    color: var(--brown); text-transform: uppercase;
  }
  .hours { font-size: 14px; font-weight: 700; color: var(--sky); margin-top: 1px; }
  .cuisine { font-size: 13px; color: var(--crimson); margin-top: 2px; }
  .motto {
    margin-top: 10px; font-family: "Lobster", cursive;
    font-size: 24px; color: var(--brown); letter-spacing: 0.5px;
  }
  .footer-band { position: absolute; left: 0; bottom: 0; width: 600px; height: 23px; }
</style>
</head>
<body>
  <div class="business-card">
    <div class="brand">
      <div class="brand-mark" role="img" aria-label="Tropical beach scene with palm tree and sunset"></div>
      <div class="brand-name">The Sunny Nook</div>
    </div>

    <div class="divider"></div>

    <div class="details">
      <p class="address">4815C Marlow Grove Avenue<br>Long Beach, California</p>
      <p class="phone">
        <svg viewBox="0 0 28 28" aria-hidden="true">
          <circle cx="14" cy="14" r="14" fill="var(--brown)"/>
          <path d="M10.2 7.5c.6-.4 1.3-.2 1.6.4l1.2 2.4c.3.6.1 1.2-.4 1.6l-.9.6c.7 1.8 2 3.2 3.8 3.9l.6-.9c.4-.5 1.1-.7 1.6-.4l2.4 1.2c.6.3.8 1 .4 1.6l-.9 1.4c-.5.7-1.4 1-2.2.8-4.2-1.2-7.3-4.3-8.5-8.5-.2-.8.1-1.7.8-2.2z" fill="#fff"/>
        </svg>
        (555) 731-2294
      </p>
      <p class="tagline">Breakfast &amp; Lunch Cafe</p>
      <p class="hours">Open 7 days a week from 7am to 2pm.</p>
      <p class="cuisine">Serving traditional American food</p>
      <p class="motto">Locals Only</p>
    </div>

    <svg class="footer-band" viewBox="0 0 600 23" preserveAspectRatio="none" aria-hidden="true">
      <polygon points="0,0 391,0 385,23 0,23" fill="var(--brown)"/>
      <polygon points="395,0 600,0 600,23 389,23" fill="var(--sky)"/>
    </svg>
  </div>
</body>
</html>
```